Fresh, modern, fun business card for pediatric dental practice

Need a business card for fresh, modern, fun pediatric dental practice

Clean look that matches our website's font and colors

We prefer the look of curved corners on business cards

Target Market(s)

parents (mothers) of young children, professionals, mid-high class

Industry/Entity Type

Dental

Contact Information for Business Card

Maplebrook Pediatric Dentistry
482 Quarry Lane
Suite 517
Fernvale, PA 17590
717.555.0193
www.maplebrookkidsdental.example

Mei-Ran Tsai, DMD
Corinne Walbeck, DMD
(we are working on our email address, but we would like that on the card as well)

Font styles to use
Sans Serif

Requirements
Must have
• All info; we would also like to make cards for individual staff members
• colors from our website and color palatte, attatched
• use same font and design as website for branding
Nice to have
• clean, simple card that has a pop of color
• we would like to see a few designs with our tag line "where smiles get brighter"
• we are not sure if we want to have it on there or not
• we would like to see a few designs incorporating the ribbon graphic on our website where the word WELCOME is

```html
<!DOCTYPE html>
<html lang="en">
<head>
<meta charset="utf-8">
<title>Maplebrook Pediatric Dentistry – Business Card</title>
<link rel="stylesheet" href="https://fonts.googleapis.com/css2?family=Work+Sans:wght@400;600;700&display=swap">
<style>
  :root {
    --backdrop: #2e2a28;
    --card: #1c1c1d;
    --sun: #fbb41f;
    --berry: #c8309f;
    --ink: #f2f2f2;
    --rule: #d9d9d9;
  }
  * { box-sizing: border-box; margin: 0; padding: 0; }
  html, body { width: 1200px; height: 715px; overflow: hidden; }
  body {
    background: var(--backdrop);
    font-family: "Work Sans", sans-serif;
    display: flex;
    align-items: center;
    justify-content: center;
    gap: 40px;
  }
  .card {
    position: relative;
    width: 520px;
    height: 297px;
    background: var(--card);
    border-radius: 16px;
    overflow: hidden;
    box-shadow: 0 10px 30px rgba(0,0,0,.35);
  }
  .brand {
    display: flex;
    align-items: flex-start;
    gap: 10px;
    color: var(--sun);
    font-weight: 600;
  }
  .brand-dot {
    flex: none;
    width: 22px; height: 22px;
    border-radius: 50%;
    background: var(--sun);
    margin-top: 8px;
  }
  .brand-name { line-height: 1.05; }
  .brand-name .main { display: block; font-size: 40px; letter-spacing: .5px; }
  .brand-name .sub { display: block; font-size: 19px; letter-spacing: 1px; }

  .card--front { display: flex; align-items: center; justify-content: center; }

  .card--back .wave { position: absolute; left: 0; top: 0; width: 520px; height: 297px; }
  .card--back .brand { position: absolute; left: 26px; top: 92px; }
  .card--back .brand-dot { width: 18px; height: 18px; margin-top: 7px; }
  .card--back .brand-name .main { font-size: 31px; }
  .card--back .brand-name .sub { font-size: 15px; }
  .card--back .divider {
    position: absolute; left: 270px; top: 78px;
    width: 1px; height: 122px; background: var(--rule);
  }
  .details { position: absolute; left: 286px; top: 74px; color: var(--ink); font-size: 11px; line-height: 1.5; }
  .details .name { color: var(--sun); font-weight: 700; font-size: 17px; letter-spacing: .5px; line-height: 1.1; }
  .details .title { font-size: 10px; margin-bottom: 8px; }
  .details .row { display: flex; align-items: center; gap: 6px; }
  .details .row svg { flex: none; width: 9px; height: 9px; }
</style>
</head>
<body>
  <section class="card card--front" aria-label="Card front">
    <div class="brand">
      <span class="brand-dot"></span>
      <span class="brand-name">
        <span class="main">maplebrook</span>
        <span class="sub">pediatric dentistry</span>
      </span>
    </div>
  </section>

  <section class="card card--back" aria-label="Card back">
    <svg class="wave" viewBox="0 0 520 297" aria-hidden="true">
      <path d="M0 240 C 90 262, 200 254, 310 262 C 410 270, 470 280, 500 297 L0 297 Z" fill="var(--sun)"/>
      <path d="M0 230 C 90 253, 200 245, 310 253 C 410 261, 472 272, 508 297" fill="none" stroke="var(--berry)" stroke-width="3"/>
    </svg>
    <div class="brand">
      <span class="brand-dot"></span>
      <span class="brand-name">
        <span class="main">maplebrook</span>
        <span class="sub">pediatric dentistry</span>
      </span>
    </div>
    <div class="divider"></div>
    <div class="details">
      <p class="name">CORINNE WALBECK</p>
      <p class="title">DMD</p>
      <p>482 Quarry Lane</p>
      <p>Suite 517 Fernvale, PA 17590</p>
      <p class="row"><svg viewBox="0 0 10 10"><path d="M2 1 L4 1 L4.6 3 L3.5 3.8 Q4.5 5.8 6.2 6.5 L7 5.4 L9 6 L9 8 Q8.5 9 7 9 Q1 7.5 1 2 Q1 1 2 1Z" fill="var(--sun)"/></svg>717.555.0193</p>
      <p class="row"><svg viewBox="0 0 10 10"><rect x="0.5" y="2" width="9" height="6" fill="none" stroke="var(--sun)"/><path d="M0.5 2 L5 5.5 L9.5 2" fill="none" stroke="var(--sun)"/></svg>hello@maplebrookkidsdental.example</p>
      <p class="row"><svg viewBox="0 0 10 10"><circle cx="5" cy="5" r="4.3" fill="none" stroke="var(--sun)"/><path d="M0.7 5 H9.3 M5 0.7 Q2.5 5 5 9.3 M5 0.7 Q7.5 5 5 9.3" fill="none" stroke="var(--sun)" stroke-width=".8"/></svg>www.maplebrookkidsdental.example</p>
    </div>
  </section>
</body>
</html>
```